Website Design Required For Education Video Portfolio Site

I am looking for a designer to create a skin for a relaunch of my website - www.brackenlearningfilms.co.uk. We want a clean and stylish new design.

The website showcases prospectus/promotional videos that are made for schools and colleges. Videos will be hosted on YouTube and embedded.

I want it to be stylish and clean.

I require 7 pages designed and this must be agreed in order to do the project.

1. Homepage
2. About
3. Prices
4. Testimonials
5. Contact Page with form
6. Promotional Videos
7. Subject Videos

The website will be then be built on the Wordpress system.

Target Market(s)

Education, Schools, Colleges, Universities

Industry/Entity Type

Education

Font styles to use
Serif

Colors

Designer to choose colors to be used in the design.

Requirements
Must have
• Video content, be clean, show our portfolio, descriptions about videos. I like the idea of having video headers.
Nice to have
• Images

```html
<!DOCTYPE html>
<html lang="en">
<head>
<meta charset="utf-8">
<title>Bracken Learning Films</title>
<link href="https://fonts.googleapis.com/css2?family=Montserrat:wght@400;500;600;700;800&display=swap" rel="stylesheet">
<style>
:root{
  --blue:#1ba8e8;
  --blue-dark:#1494d4;
  --ink:#111;
  --grey:#777;
  --line:#e6e6e6;
  --white:#fff;
  --black:#0b0b0b;
}
*{box-sizing:border-box;margin:0;padding:0}
html,body{width:1200px;height:4532px;overflow:hidden}
body{font-family:'Montserrat',sans-serif;color:var(--ink);background:var(--white);position:relative}
.abs{position:absolute}
.site-header{position:absolute;top:0;left:0;width:1200px;height:84px;background:var(--white)}
.brand{position:absolute;left:94px;top:18px;display:flex;align-items:center;gap:10px}
.brand-mark{width:44px;height:44px;border-radius:50%;background:var(--blue)}
.brand-name{font-weight:800;font-size:34px;color:var(--blue);line-height:1}
.nav{position:absolute;right:96px;top:34px;display:flex;gap:26px;font-size:14px;font-weight:600}
.hero{position:absolute;top:84px;left:0;width:1200px;height:558px;background:linear-gradient(100deg,#6f6253 0%,#b9a48a 35%,#8fb7b6 65%,#4e7f86 100%)}
.hero h1{position:absolute;left:112px;top:112px;color:var(--white);font-size:51px;font-weight:800;line-height:50px;text-transform:uppercase}
.btn-outline{position:absolute;border:2px solid var(--white);color:var(--white);border-radius:12px;font-weight:700;font-size:15px;display:flex;align-items:center;justify-content:center}
.btn{position:absolute;background:var(--blue);color:var(--white);border-radius:12px;font-weight:700;font-size:15px;display:flex;align-items:center;justify-content:center}
.photo{position:absolute;border:6px solid var(--blue);border-radius:18px}
.about-title{left:600px;top:730px;font-size:36px;font-weight:700}
.about-lead{left:600px;top:784px;width:480px;font-size:20px;font-weight:600;line-height:30px}
.about-body{left:600px;top:916px;width:470px;font-size:13px;color:var(--grey);line-height:26px}
.section-title{position:absolute;left:0;width:1200px;text-align:center;font-size:37px;font-weight:700}
.section-sub{position:absolute;left:200px;width:800px;text-align:center;font-size:13.5px;color:var(--grey);line-height:26px}
.card{position:absolute;background:var(--white);border-radius:12px;box-shadow:0 4px 18px rgba(0,0,0,.12);overflow:hidden}
.card .thumb{position:absolute;left:5px;top:5px;right:5px;border-radius:8px}
.card .label{position:absolute;left:10px;right:10px;text-align:center;font-weight:700;font-size:21px;line-height:30px}
.play{position:absolute;width:50px;height:50px;border-radius:50%;background:#2ec4b6;left:50%;margin-left:-25px}
.play::after{content:"";position:absolute;left:20px;top:15px;border-left:15px solid var(--white);border-top:10px solid transparent;border-bottom:10px solid transparent}
.arrow{position:absolute;width:36px;height:36px;border-radius:50%}
.arrow.prev{background:#d8d8d8}
.arrow.next{background:var(--blue)}
.arrow svg{position:absolute;left:11px;top:11px}
.price-band{position:absolute;top:1727px;left:0;width:1200px;height:733px;background:linear-gradient(180deg,#1ba8e8,#23a9e6)}
.price-card .title{position:absolute;left:8px;right:8px;top:204px;text-align:center;font-size:18px;font-weight:600;line-height:27px;white-space:nowrap}
.price-card .desc{position:absolute;left:14px;right:14px;text-align:center;font-size:13px;color:var(--grey);line-height:26px;overflow:hidden;white-space:nowrap}
.testimonial-card{left:465px;top:2654px;width:583px;height:368px}
.quote-name{left:580px;top:2700px;font-weight:700;font-size:16px}
.quote-role{left:582px;top:2726px;font-size:13px}
.quote-text{left:582px;top:2756px;width:440px;font-size:13px;color:var(--grey);line-height:26px}
.contact-band{position:absolute;top:3620px;left:0;width:1200px;height:530px;background:linear-gradient(135deg,#1ba8e8,#4cc4f2)}
.contact-band h2{position:absolute;top:86px;left:0;width:1200px;text-align:center;color:var(--white);font-size:37px;font-weight:700}
.info{position:absolute;left:112px;display:flex;gap:14px;color:var(--white);font-weight:700;font-size:15px;line-height:26px}
.info .ico{width:38px;height:38px;border:2px solid var(--white);border-radius:50%;flex:none;display:flex;align-items:center;justify-content:center}
.field{position:absolute;background:var(--white);border-radius:4px;font-size:13px;color:var(--grey);padding:12px 16px}
.site-footer{position:absolute;top:4150px;left:0;width:1200px;height:382px;background:var(--black);color:var(--white)}
.site-footer h3{position:absolute;top:85px;font-size:23px;font-weight:700}
.site-footer ul{position:absolute;top:132px;list-style:none;font-size:13.5px;line-height:30px}
.footer-brand{position:absolute;left:888px;top:88px;display:flex;align-items:center;gap:10px}
.footer-brand .brand-mark{width:40px;height:40px}
.footer-brand .brand-name{font-size:27px}
.footer-about{position:absolute;left:892px;top:140px;width:230px;font-size:13.5px;line-height:30px}
.footer-rule{position:absolute;left:105px;top:322px;width:980px;height:1px;background:#444}
.copyright{position:absolute;top:348px;left:0;width:1200px;text-align:center;font-size:13px}
</style>
</head>
<body>

<header class="site-header">
  <div class="brand"><span class="brand-mark"></span><span class="brand-name">Bracken</span></div>
  <nav class="nav"><span>About</span><span>Prices</span><span>Testimonials</span><span>Contact</span><span>Promotional Videos</span><span>Subject Videos</span></nav>
</header>

<section class="hero" role="img" aria-label="Excited school children running down a bright school corridor">
  <h1>We make<br>awesome<br>educational<br>videos</h1>
  <div class="btn-outline" style="left:112px;top:349px;width:136px;height:44px">Get Started</div>
</section>

<section class="about">
  <div class="photo" role="img" aria-label="Smiling group of students with backpacks" style="left:115px;top:733px;width:453px;height:359px;background:linear-gradient(160deg,#9b8c78,#4d6f86)"></div>
  <h2 class="abs about-title">About Us</h2>
  <p class="abs about-lead">Hi, I'm Daniel Hartley, Videographer,<br>Content Creator, Filmmaker. Founder of<br>Bracken Learning Films and dad of<br>two. Thanks for stopping by.</p>
  <p class="abs about-body">I've been producing all kinds of videos for over 25 years<br>(from weddings and other live events to corporate and<br>educational promotions – it's truly the best job in the world).<br>At the age of eight, I was bitten by the videomaking bug</p>
  <div class="btn" style="left:600px;top:1040px;width:137px;height:46px">Read More</div>
</section>

<section class="promo">
  <h2 class="section-title" style="top:1168px">Promotional Videos</h2>
  <p class="section-sub" style="top:1228px">Take a look at some of the videos we have produced for schools, colleges and training providers in the<br>North of England.</p>
  <div class="arrow prev" style="left:32px;top:1449px"><svg width="14" height="14" viewBox="0 0 14 14"><path d="M9 2 4 7l5 5" stroke="#fff" stroke-width="2" fill="none"/></svg></div>
  <div class="card" style="left:110px;top:1305px;width:305px;height:325px">
    <div class="thumb" role="img" aria-label="Aerial view of a primary school playground" style="height:208px;background:linear-gradient(135deg,#7f8a6a,#5c8c4a)"></div>
    <div class="play" style="top:86px"></div>
    <div class="label" style="top:236px">Willowmere Primary<br>School</div>
  </div>
  <div class="card" style="left:448px;top:1305px;width:304px;height:325px">
    <div class="thumb" role="img" aria-label="Aerial view of an academy campus" style="height:208px;background:linear-gradient(135deg,#7a8676,#566b7a)"></div>
    <div class="play" style="top:86px"></div>
    <div class="label" style="top:220px">Harbourside Academy,<br>Eastwick, County<br>Durham</div>
  </div>
  <div class="card" style="left:785px;top:1305px;width:303px;height:325px">
    <div class="thumb" role="img" aria-label="Aerial view of a school and surrounding fields" style="height:208px;background:linear-gradient(135deg,#7e8c6c,#5e8a52)"></div>
    <div class="play" style="top:86px"></div>
    <div class="label" style="top:230px">Kingsford Primary<br>School, South Moor</div>
  </div>
  <div class="arrow next" style="left:1121px;top:1449px"><svg width="14" height="14" viewBox="0 0 14 14"><path d="M5 2l5 5-5 5" stroke="#fff" stroke-width="2" fill="none"/></svg></div>
</section>

<section class="price-band">
  <h2 class="section-title" style="top:70px;color:var(--white)">Price Guide</h2>
  <div class="arrow prev" style="left:32px;top:333px;background:#e8e8e8"><svg width="14" height="14" viewBox="0 0 14 14"><path d="M9 2 4 7l5 5" stroke="#999" stroke-width="2" fill="none"/></svg></div>
  <div class="card price-card" style="left:110px;top:153px;width:307px;height:407px">
    <div class="thumb" role="img" aria-label="Pupil playing a brass instrument" style="height:186px;background:linear-gradient(135deg,#3f5f9e,#c9a24a)"></div>
    <div class="title">Subject Videos – prices start<br>at £1,200</div>
    <div class="desc" style="top:258px">We help you showcase your lessons<br>via a series of 30-60 second videos<br>for you to use across your website or</div>
    <div class="btn" style="left:84px;top:342px;width:138px;height:46px">Explore</div>
  </div>
  <div class="card price-card" style="left:446px;top:153px;width:307px;height:407px">
    <div class="thumb" role="img" aria-label="Young children looking at pictures on the grass" style="height:186px;background:linear-gradient(135deg,#6f7a5a,#5b6d8a)"></div>
    <div class="title">Prospectus Videos<br>(Interview based) – prices<br>start at £1,200</div>
    <div class="desc" style="top:284px">Through interviews with the people<br>who know it best</div>
    <div class="btn" style="left:84px;top:342px;width:138px;height:46px">Explore</div>
  </div>
  <div class="card price-card" style="left:782px;top:153px;width:307px;height:407px">
    <div class="thumb" role="img" aria-label="Smiling pupil in a school hall" style="height:186px;background:linear-gradient(135deg,#8f7c6a,#3f5f8a)"></div>
    <div class="title">Promotional Videos (Music<br>based) – prices start at<br>£1,200</div>
    <div class="desc" style="top:284px">Affordable, music-driven videos that<br>highlight your special events are an</div>
    <div class="btn" style="left:84px;top:342px;width:138px;height:46px">Explore</div>
  </div>
  <div class="arrow next" style="left:1121px;top:333px;background:var(--white)"><svg width="14" height="14" viewBox="0 0 14 14"><path d="M5 2l5 5-5 5" stroke="#1ba8e8" stroke-width="2" fill="none"/></svg></div>
  <div class="btn-outline" style="left:530px;top:606px;width:139px;height:47px">View All</div>
</section>

<section class="testimonials">
  <h2 class="section-title" style="top:2525px">Testimonials</h2>
  <div class="card testimonial-card"></div>
  <div class="photo" role="img" aria-label="Two pupils outside a school entrance" style="left:137px;top:2612px;width:391px;height:325px;background:linear-gradient(135deg,#8c8578,#3b3f5a)"></div>
  <div class="play" style="left:518px;top:2752px"></div>
  <div class="abs quote-name">CAROL BENTON,</div>
  <div class="abs quote-role">Head teacher, Ashbrook Primary School, Hexley</div>
  <p class="abs quote-text">I just wanted to say a huge thank you for our fabulous Christmas film. It is relaxed and organic and totally captures the spirit or the school. I love the fact it is all about the children. I can't wait to share it with the parent. Thanks again and we will definitely keep you in mind for future events and recommend you to other schools.</p>
  <svg class="abs" style="left:880px;top:2965px" width="102" height="14" viewBox="0 0 102 14"><path d="M42 7H2m6-5L2 7l6 5" stroke="#333" stroke-width="1.5" fill="none"/><path d="M58 7h40m-6-5 6 5-6 5" stroke="#1ba8e8" stroke-width="1.5" fill="none"/></svg>
</section>

<section class="subjects">
  <h2 class="section-title" style="top:3105px">Subject Videos</h2>
  <p class="section-sub" style="top:3165px">Our multi-video packages are perfect for your school website to show the likes of Edvera the breadth of<br>your curriculum as well as showcase to parents the great lessons you do.</p>
  <div class="arrow prev" style="left:32px;top:3386px"><svg width="14" height="14" viewBox="0 0 14 14"><path d="M9 2 4 7l5 5" stroke="#fff" stroke-width="2" fill="none"/></svg></div>
  <div class="card" style="left:110px;top:3243px;width:305px;height:282px">
    <div class="thumb" role="img" aria-label="Pupils pointing at a wall map" style="height:202px;background:linear-gradient(135deg,#b98aa0,#6f8fb8)"></div>
    <div class="play" style="top:84px"></div>
    <div class="label" style="top:226px">Geography</div>
  </div>
  <div class="card" style="left:448px;top:3243px;width:304px;height:282px">
    <div class="thumb" role="img" aria-label="Pupil wearing safety goggles in a science lesson" style="height:202px;background:linear-gradient(135deg,#9aa7b3,#5d6f7e)"></div>
    <div class="play" style="top:84px"></div>
    <div class="label" style="top:226px">Science</div>
  </div>
  <div class="card" style="left:785px;top:3243px;width:303px;height:282px">
    <div class="thumb" role="img" aria-label="Nursery child playing at a table" style="height:202px;background:linear-gradient(135deg,#7c8a6f,#3fa8a0)"></div>
    <div class="play" style="top:84px"></div>
    <div class="label" style="top:226px">Nursery</div>
  </div>
  <div class="arrow next" style="left:1121px;top:3386px"><svg width="14" height="14" viewBox="0 0 14 14"><path d="M5 2l5 5-5 5" stroke="#fff" stroke-width="2" fill="none"/></svg></div>
</section>

<section class="contact-band">
  <h2>Contact Us</h2>
  <div class="info" style="top:146px"><span class="ico"><svg width="16" height="18" viewBox="0 0 16 18"><path d="M8 17s6-6 6-10A6 6 0 0 0 2 7c0 4 6 10 6 10z" fill="none" stroke="#fff" stroke-width="1.6"/><circle cx="8" cy="7" r="2" fill="#fff"/></svg></span><span>Unit 4, Fernbank Business<br>Park, Hollinside, Durham. DH8 2QX.</span></div>
  <div class="info" style="top:226px;align-items:center"><span class="ico"><svg width="16" height="16" viewBox="0 0 16 16"><path d="M3 1l3 3-2 2a9 9 0 0 0 6 6l2-2 3 3-2 2C7 15 1 9 1 3z" fill="#fff"/></svg></span><span>01632 960 418</span></div>
  <div class="info" style="top:282px;align-items:center"><span class="ico"><svg width="18" height="14" viewBox="0 0 18 14"><rect x="1" y="1" width="16" height="12" fill="none" stroke="#fff" stroke-width="1.6"/><path d="M1 1l8 7 8-7" fill="none" stroke="#fff" stroke-width="1.6"/></svg></span><span>info@brackenlearningfilms.co.uk</span></div>
  <div class="field" style="left:502px;top:143px;width:280px;height:45px">First Name</div>
  <div class="field" style="left:803px;top:143px;width:282px;height:45px">Last Name</div>
  <div class="field" style="left:502px;top:206px;width:280px;height:45px">Email</div>
  <div class="field" style="left:803px;top:206px;width:282px;height:45px">Phone</div>
  <div class="field" style="left:502px;top:270px;width:583px;height:100px">Message</div>
  <div class="btn-outline" style="left:502px;top:398px;width:176px;height:46px">Submit</div>
</section>

<footer class="site-footer">
  <h3 style="left:105px">Main Links</h3>
  <ul style="left:105px"><li>About</li><li>Prices</li><li>Testimonials</li><li>Contact</li><li>Promotional Videos</li><li>Subject Videos</li></ul>
  <h3 style="left:350px">Other Links</h3>
  <ul style="left:354px"><li>Terms and Conditions</li><li>Privacy Policy</li><li>Careers</li></ul>
  <h3 style="left:592px">Contact Info</h3>
  <ul style="left:595px;width:240px"><li>☏ 01632 960 418</li><li>✉ info@brackenlearningfilms.co.uk</li><li>⌖ Unit 4, Fernbank Business Park, Hollinside, Durham. DH8 2QX.</li></ul>
  <div class="footer-brand"><span class="brand-mark"></span><span class="brand-name">Bracken</span></div>
  <p class="footer-about">Striving to deliver quality video content for schools and colleges in the North of England.</p>
  <div class="footer-rule"></div>
  <p class="copyright">© 2023 Bracken Learning Films. All rights reserved</p>
</footer>

</body>
</html>
```